New Fun, Positive, energised looking Business Card Needed for High Achiever Coach

I am looking for a two sided full colour business card. I am self employed and have recently re branded my 1-2-1 work Renewing Driven Leaders. My target client base for these cards is therefore high achievers - usually aged 40 -55, they are often entrepreneurs, CEO or work in banking and finance and 2/3 are male. I work with them on 90 day or 6 month coaching programs to help them live their success in a healthier, more sustainable and fulfiiled way. They pay for this privately so though they are corporate types the cards need not look 'corporate'. I want to portray the idea of transformation, vitality and re-connecting.
You can get a feel for the look I like on my new website: morvenlisk.co.uk
I want to use this logo with strapline (Renewing Driven Leaders) (I purchased off Logoharbor) and font/ colours (the turquoise and green).
Details to include on the card:
www.morvenlisk.co.uk
+44 7915 302618
morven@morvenlisk.co.uk
skype: morvenlisk
I'd also like to include:
Do you struggle to switch off? Want to be healthier and feel fitter? Want closer relationships? More clarity over the direction you are headed? I can help you do these things using integrated mind-body techniques. Visit morvenlisk.co.uk TODAY to apply for a FREE Breakthrough session.
BUT if that is too much text for a card I am open to advice/ammendments.
Updates
Thanks for your design - I am considering them. PLease change the wording to :

```html
<!DOCTYPE html>
<html lang="en">
<head>
<meta charset="utf-8">
<title>Morven Lisk – Business Card</title>
<link href="https://fonts.googleapis.com/css2?family=Open+Sans:wght@400;600;800&display=swap" rel="stylesheet">
<style>
  :root {
    --backdrop: #e6e6ea;
    --card-white: #ffffff;
    --brand-green: #62b96c;
    --brand-turquoise: #19a6cf;
    --ink: #2b2b2b;
    --rule: #c9c9c9;
    --on-green: #ffffff;
  }
  * { margin: 0; padding: 0; box-sizing: border-box; }
  html, body {
    width: 1200px; height: 987px; overflow: hidden;
    background: var(--backdrop);
    font-family: "Open Sans", sans-serif;
  }
  .sheet {
    position: relative; width: 1200px; height: 987px;
    display: flex; flex-direction: column; align-items: center; justify-content: center;
    gap: 60px;
  }
  .card {
    width: 700px; height: 400px; border-radius: 34px;
    box-shadow: 0 6px 18px rgba(0,0,0,0.12);
    position: relative; overflow: hidden;
  }
  /* Back side */
  .card--back {
    background: var(--brand-green);
    color: var(--on-green);
    display: flex; align-items: center; justify-content: center;
    text-align: center;
  }
  .pitch { font-size: 21px; line-height: 1.3; font-weight: 400; }
  .pitch p + p { margin-top: 14px; }
  .pitch strong { font-weight: 800; }
  /* Front side */
  .card--front { background: var(--card-white); }
  .identity {
    position: absolute; top: 70px; left: 0; right: 0;
    display: flex; flex-direction: column; align-items: center;
  }
  .identity__mark {
    width: 70px; height: 70px; border-radius: 50%;
    background: var(--brand-green); margin-bottom: 16px;
  }
  .identity__name {
    font-size: 46px; font-weight: 800; color: var(--brand-turquoise);
    letter-spacing: 1px; line-height: 1;
  }
  .identity__strapline {
    margin-top: 8px; font-size: 19px; font-weight: 400;
    color: var(--brand-turquoise);
  }
  .rule {
    position: absolute; left: 70px; right: 70px; height: 1px;
    background: linear-gradient(90deg, transparent, var(--rule) 15%, var(--rule) 85%, transparent);
  }
  .rule--top { top: 44px; }
  .rule--bottom { bottom: 36px; }
  .contacts {
    position: absolute; left: 70px; right: 70px; bottom: 62px;
    display: grid; grid-template-columns: auto auto; justify-content: center;
    column-gap: 34px; row-gap: 12px;
    font-size: 20px; color: var(--ink);
  }
  .contact { display: flex; align-items: center; gap: 9px; }
  .contact svg { width: 20px; height: 20px; flex: none; }
  .contact__dot {
    width: 18px; height: 18px; border-radius: 50%;
    background: var(--brand-turquoise); flex: none;
  }
</style>
</head>
<body>
<main class="sheet">

  <section class="card card--back" aria-label="Card back">
    <div class="pitch">
      <p>Do you struggle to switch off?<br>
      Want to be healthier and feel fitter?<br>
      Want closer relationships?<br>
      More clarity over the direction you are headed?<br>
      I can help you do these things using integrated<br>
      mind-body techniques.</p>
      <p>Visit <strong>morvenlisk.co.uk</strong> TODAY to apply for a<br>
      FREE Breakthrough session.</p>
    </div>
  </section>

  <section class="card card--front" aria-label="Card front">
    <div class="rule rule--top"></div>
    <div class="identity">
      <div class="identity__mark"></div>
      <div class="identity__name">Morven Lisk</div>
      <div class="identity__strapline">Renewing Driven Leaders</div>
    </div>
    <div class="contacts">
      <div class="contact">
        <svg viewBox="0 0 20 20" aria-hidden="true"><circle cx="10" cy="10" r="9" fill="none" stroke="var(--brand-turquoise)" stroke-width="1.6"/><path d="M7 5.5l2 2-1 1.2c.6 1.3 1.6 2.3 2.9 2.9l1.2-1 2 2-1.3 1.6c-3.6-.4-6.5-3.3-6.9-6.9z" fill="var(--brand-turquoise)"/></svg>
        <span>+44 7915 302618</span>
      </div>
      <div class="contact">
        <svg viewBox="0 0 20 20" aria-hidden="true"><rect x="1.5" y="4" width="17" height="12" rx="2" fill="var(--brand-turquoise)"/><path d="M2.5 5l7.5 6 7.5-6" fill="none" stroke="#fff" stroke-width="1.5"/></svg>
        <span>morven@morvenlisk.co.uk</span>
      </div>
      <div class="contact">
        <svg viewBox="0 0 20 20" aria-hidden="true"><circle cx="10" cy="10" r="9" fill="var(--brand-turquoise)"/><g fill="none" stroke="#fff" stroke-width="1.1"><ellipse cx="10" cy="10" rx="4" ry="8.5"/><path d="M1.5 10h17M3 5.5h14M3 14.5h14"/></g></svg>
        <span>www.morvenlisk.co.uk</span>
      </div>
      <div class="contact">
        <span class="contact__dot"></span>
        <span>morvenlisk</span>
      </div>
    </div>
    <div class="rule rule--bottom"></div>
  </section>

</main>
</body>
</html>
```